Creative, fresh business card design for Ripplecraft Facades

We need a fresh, creative business card design for Ripplecraft Facades. We are the manufacturer of Ripplecraft Facades in Australia. Wall panels are 2400 x 1200mm panels made from MDF and feature 3D patterns on the face of the panel. The colours to be used are green, silver/grey and white RGB
Red 187
Green 207
Blue 65.

An idea is to possibly use a watermark of one of our designs as a background (like on the "Grids" design on the left hand side of page 2 of our brochure).

Target Market(s)

Interior designers, architects, builders and home renovators

Industry/Entity Type

Business

Contact Information for Business Card

Details to go on the card are:
Our logo (attached),
Slogan: "Decorative panels for interiors and exteriors",
Contact name,
Position,
Mobile phone number,
Business address,
Business phone,
Business fax,
Website and
Email address.

I have attached a few images of our panels and our brochure for reference.

The colours of the business card should feature our logo colours which are: RGB
Red 187
Green 207
Blue 65

Requirements
Must have
• Very modern fonts and design. Some of the designs shown especially the "Prisms" design which is a popular design.
Nice to have
• Creative but simple design. Very contemporary.
Should not have
• Anything ornate or old fashioned.

```html
<!DOCTYPE html>
<html lang="en">
<head>
<meta charset="utf-8">
<title>Ripplecraft Facades – Business Cards</title>
<link rel="stylesheet" href="https://fonts.googleapis.com/css2?family=Arimo:wght@400;700&display=swap">
<style>
  :root {
    --brand-green: rgb(187, 207, 65);
    --card-green: #c2d62e;
    --silver: #939598;
    --slogan-grey: #8a8c8e;
    --paper: #ffffff;
    --backdrop: #e9eaeb;
    --panel-dark: #4a4b4d;
    --panel-light: #b9babc;
  }
  * { box-sizing: border-box; margin: 0; padding: 0; }
  html, body {
    width: 1200px; height: 900px; overflow: hidden;
    background: var(--backdrop);
    font-family: "Arimo", Arial, sans-serif;
  }
  .sheet { position: relative; width: 1200px; height: 900px; }
  .card {
    position: absolute;
    width: 490px; height: 298px;
    background: var(--paper);
    box-shadow: 0 2px 8px rgba(0,0,0,0.15);
  }
  .card--tl { left: 72px;  top: 138px; }
  .card--tr { left: 615px; top: 138px; }
  .card--bl { left: 72px;  top: 464px; }
  .card--br { left: 615px; top: 464px; }

  .person {
    position: absolute; left: 21px; top: 21px;
    width: 176px; height: 126px;
    background: var(--silver);
    color: var(--paper);
    padding: 31px 0 0 17px;
    font-size: 13.5px; line-height: 17px;
  }
  .person__name { font-weight: 700; }
  .person__mobile { margin-top: 17px; }
  .person__mobile b { font-weight: 700; }

  .panel-photo {
    position: absolute; left: 201px; top: 21px;
    width: 268px; height: 126px;
    background: linear-gradient(100deg, var(--panel-dark) 0%, #6e6f71 45%, var(--panel-light) 100%);
  }

  .slogan {
    position: absolute; left: 21px; top: 153px; width: 448px;
    text-align: center;
    font-size: 15px; letter-spacing: 3.1px;
    color: var(--slogan-grey);
    white-space: nowrap;
  }

  .brand {
    position: absolute; left: 21px; top: 175px;
    width: 176px; height: 102px;
    background: var(--card-green);
    color: var(--paper);
    display: flex; align-items: center;
    padding-left: 16px;
    font-weight: 700; font-size: 22px; line-height: 25px;
  }

  .contact {
    position: absolute; left: 201px; top: 175px;
    width: 268px; height: 102px;
    background: var(--card-green);
    color: var(--paper);
    padding: 17px 0 0 16px;
    font-size: 12.5px; line-height: 17px;
    white-space: nowrap;
  }
  .contact b { font-weight: 700; }
</style>
</head>
<body>
<main class="sheet">

  <article class="card card--tl">
    <div class="person">
      <p class="person__name">Julian Verhoeven</p>
      <p class="person__role">General Manager</p>
      <p class="person__mobile">M <b>0412 555 301</b></p>
    </div>
    <div class="panel-photo" role="img" aria-label="Photograph of a grey rippled 3D wall panel in a modern interior"></div>
    <p class="slogan">decorative panels for interiors &amp; exteriors</p>
    <div class="brand">Ripplecraft<br>Facades</div>
    <div class="contact">
      <p>P <b>02 9461 3080</b>&nbsp; F <b>02 9461 3081</b></p>
      <p>14 Kestrel Road, Marlow Vale NSW 2190</p>
      <p>sales@ripplecraftfacades.com.au</p>
      <p><b>www.ripplecraftfacades.com.au</b></p>
    </div>
  </article>

  <article class="card card--tr">
    <div class="person">
      <p class="person__name">Patrick Fenwick</p>
      <p class="person__role">Production Manager</p>
      <p class="person__mobile">M <b>0412 555 318</b></p>
    </div>
    <div class="panel-photo" role="img" aria-label="Photograph of a grey rippled 3D wall panel in a modern interior"></div>
    <p class="slogan">decorative panels for interiors &amp; exteriors</p>
    <div class="brand">Ripplecraft<br>Facades</div>
    <div class="contact">
      <p>P <b>02 9461 3080</b>&nbsp; F <b>02 9461 3081</b></p>
      <p>14 Kestrel Road, Marlow Vale NSW 2190</p>
      <p>sales@ripplecraftfacades.com.au</p>
      <p><b>www.ripplecraftfacades.com.au</b></p>
    </div>
  </article>

  <article class="card card--bl">
    <div class="person">
      <p class="person__name">Tessa Harland</p>
      <p class="person__role">Office administrator</p>
      <p class="person__mobile">M <b>0412 555 326</b></p>
    </div>
    <div class="panel-photo" role="img" aria-label="Photograph of a grey rippled 3D wall panel in a modern interior"></div>
    <p class="slogan">decorative panels for interiors &amp; exteriors</p>
    <div class="brand">Ripplecraft<br>Facades</div>
    <div class="contact">
      <p>P <b>02 9461 3080</b>&nbsp; F <b>02 9461 3081</b></p>
      <p>14 Kestrel Road, Marlow Vale NSW 2190</p>
      <p>sales@ripplecraftfacades.com.au</p>
      <p><b>www.ripplecraftfacades.com.au</b></p>
    </div>
  </article>

  <article class="card card--br">
    <div class="person">
      <p class="person__name">Leona Hartigan</p>
      <p class="person__role">Office administrator</p>
      <p class="person__mobile">M <b>0412 555 347</b></p>
    </div>
    <div class="panel-photo" role="img" aria-label="Photograph of a grey rippled 3D wall panel in a modern interior"></div>
    <p class="slogan">decorative panels for interiors &amp; exteriors</p>
    <div class="brand">Ripplecraft<br>Facades</div>
    <div class="contact">
      <p>P <b>02 9461 3080</b>&nbsp; F <b>02 9461 3081</b></p>
      <p>14 Kestrel Road, Marlow Vale NSW 2190</p>
      <p>sales@ripplecraftfacades.com.au</p>
      <p><b>www.ripplecraftfacades.com.au</b></p>
    </div>
  </article>

</main>
</body>
</html>
```